Online shopping portal - Business Card Design

Brivamart.com.au is a complete shopping experience. Search, compare & buy items from partnered stores & receive cashbash for your purchases and referrals.
Mission
Our mission is to provide a system for entrepreneurs to create an ongoing income, while providing consumers worldwide with a better way to shop.
A product brokerage and Internet marketing company that specialises in One-to-One Marketing, Quellon Oceania is a subsidiary of Dorvex Holdings Global, Inc.
With more than 3 million Preferred Customers and 180,000 Customer Managers worldwide, Dorvex Holdings has generated over $3 billion USD in accumulated retail sales. The Company employs more than 675 people globally with international operations in Australia, United States, Canada, Taiwan, Hong Kong, Mexico & Singapore
Through revolutionary technology and the one-to-one marketing and social shopping Quellon Oceania are leveraging the Internet with the power of people to create the economy of the future.
By providing online shoppers with the products and services they want and need — backed by the Company’s people power — Quellon Oceania is fast becoming the World Wide Web’s ultimate online shopping destination.
As a result, we are changing the way people shop and changing the economic paradigm where anyone can become financially independent by creating their own economy — Made with Goods. Driven by Folks®.
Description
Welcome to a new kind of comparison shopping site where you get PAID cashback to shop!
Simply create an account to start accumulating cash backs each time you make purchases across hundreds of trusted Partner Stores and thousands of your favorite brands through our convenient PixBasket® for one stop shopping.
All merchant stores are backed by GLIMVEN.NET's 100% satisfaction guarantee.

Updates
Project Deadline Extended
Reason: Hi all,  I am extending the deadline as i'm going to be away for my birthday (and may not have time to check before the current deadline anyway)  I figure that the more time i give you the better.

Industry/Entity Type
Online Shopping
Contact Information for Business Card
Business Name: Brivamart.com.au
website: www.brivamart.com.au
Friendlane: www.friendlane.net/brivamart.com.au.
Email: info@brivamart.com.au
Phone: Lorn on 0487 52 19 64
Requirements
Nice to have
- Create a Brivamart logo

```html
<!DOCTYPE html>
<html lang="en">
<head>
<meta charset="utf-8">
<title>Brivamart.com.au – Business Card</title>
<link rel="stylesheet" href="https://fonts.googleapis.com/css2?family=Open+Sans:wght@700;800&family=Ubuntu:wght@500;700&display=swap">
<style>
  :root {
    --teal: #007a72;
    --white: #ffffff;
    --paper: #f4f5f5;
    --paper-shade: #d9dcdc;
    --backdrop: #3b3532;
    --icon-fill: #e8f2f1;
  }
  * { margin: 0; padding: 0; box-sizing: border-box; }
  html, body {
    width: 1200px; height: 799px; overflow: hidden;
    background: var(--backdrop);
  }
  .stage {
    position: relative; width: 1200px; height: 799px;
    display: flex; align-items: center; justify-content: center; gap: 60px;
  }
  .card {
    width: 520px; height: 320px; border-radius: 14px;
    position: relative; overflow: hidden;
    box-shadow: 0 10px 30px rgba(0,0,0,.45);
  }

  /* Front */
  .card-front { background: var(--teal); color: var(--white); font-family: "Open Sans", sans-serif; }
  .brand {
    position: absolute; top: 48px; left: 0; right: 0;
    display: flex; flex-direction: column; align-items: center; gap: 10px;
  }
  .brand-dot { width: 56px; height: 56px; border-radius: 50%; background: var(--white); }
  .brand-name { font-size: 34px; font-weight: 800; color: var(--white); line-height: 1.1; }
  .steps {
    position: absolute; left: 40px; right: 40px; bottom: 44px;
    display: flex; justify-content: space-between;
    list-style: none;
  }
  .step { display: flex; flex-direction: column; align-items: center; gap: 8px; width: 100px; }
  .step-icon { width: 40px; height: 40px; }
  .step-icon.placeholder { background: var(--icon-fill); border-radius: 8px; opacity: .9; }
  .step-label { font-size: 17px; font-weight: 700; line-height: 1.2; }

  /* Back */
  .card-back {
    background: linear-gradient(160deg, var(--paper-shade) 0%, var(--paper) 35%, var(--white) 100%);
    color: var(--teal); font-family: "Ubuntu", sans-serif; text-align: center;
  }
  .back-brand {
    margin-top: 36px; display: flex; align-items: center; justify-content: center; gap: 12px;
  }
  .back-brand .brand-dot { width: 48px; height: 48px; background: var(--teal); }
  .back-brand .brand-name { font-family: "Ubuntu", sans-serif; font-weight: 700; font-size: 26px; color: var(--teal); }
  .tagline { margin-top: 16px; font-size: 34px; font-weight: 700; line-height: 1.15; color: var(--teal); }
  .contacts { margin-top: 12px; list-style: none; font-size: 15px; font-weight: 500; line-height: 1.35; }
  .phone { margin-top: 10px; font-size: 25px; font-weight: 700; letter-spacing: 1px; line-height: 1.2; }
</style>
</head>
<body>
<main class="stage">
  <section class="card card-front" aria-label="Business card front">
    <div class="brand">
      <span class="brand-dot"></span>
      <span class="brand-name">Brivamart.com.au</span>
    </div>
    <ul class="steps">
      <li class="step">
        <svg class="step-icon" viewBox="0 0 40 40" aria-hidden="true">
          <circle cx="17" cy="16" r="10" fill="none" stroke="var(--white)" stroke-width="4"/>
          <line x1="24" y1="23" x2="34" y2="34" stroke="var(--white)" stroke-width="5" stroke-linecap="round"/>
        </svg>
        <span class="step-label">Search</span>
      </li>
      <li class="step">
        <span class="step-icon placeholder" role="img" aria-label="Shopping bags icon"></span>
        <span class="step-label">Compare</span>
      </li>
      <li class="step">
        <span class="step-icon placeholder" role="img" aria-label="Shopping basket icon"></span>
        <span class="step-label">Buy</span>
      </li>
      <li class="step">
        <span class="step-icon placeholder" role="img" aria-label="Banknotes icon"></span>
        <span class="step-label">Earn</span>
      </li>
    </ul>
  </section>

  <section class="card card-back" aria-label="Business card back">
    <div class="back-brand">
      <span class="brand-dot"></span>
      <span class="brand-name">Brivamart</span>
    </div>
    <h1 class="tagline">Get paid to shop</h1>
    <ul class="contacts">
      <li>Website: www.brivamart.com.au</li>
      <li>Friendlane: www.friendlane.net/brivamart.com.au.</li>
      <li>Email: info@brivamart.com.au</li>
    </ul>
    <p class="phone">0487 52 19 64</p>
  </section>
</main>
</body>
</html>
```